Software allocation system needs a business card design

We need a business card designed for our software platform - www.tallivo.com.au

At the moment the logo and website is all black and white, we are happy for suggestions on implementing some colour throughout either the logo or business card.

Industry/Entity Type

Software

Font styles to use
Sans Serif

Colors

Designer to choose colors to be used in the design.

```html
<!DOCTYPE html>
<html lang="en">
<head>
<meta charset="utf-8">
<title>Tallivo Business Card</title>
<link rel="stylesheet" href="https://fonts.googleapis.com/css2?family=Montserrat:wght@400;700&family=Encode+Sans+Condensed:wght@500&family=Cabin:wght@400&display=swap">
<style>
  :root {
    --paper: #f0f0f0;
    --ink: #111111;
    --ink-soft: #444444;
    --accent: #5bbbe8;
    --rule: #222222;
  }
  html, body { margin: 0; padding: 0; overflow: hidden; background: var(--paper); }
  .card {
    position: relative;
    width: 686px;
    height: 1200px;
    background: var(--paper);
    overflow: hidden;
    color: var(--ink);
  }
  .accent-tab {
    position: absolute;
    left: 149px;
    width: 388px;
    height: 8px;
    background: var(--accent);
  }
  .accent-tab.top { top: 0; border-radius: 0 0 6px 6px; }
  .accent-tab.bottom { bottom: 0; border-radius: 6px 6px 0 0; }
  .brand {
    position: absolute;
    top: 172px;
    left: 0;
    width: 686px;
    display: flex;
    justify-content: center;
    align-items: center;
    gap: 18px;
  }
  .brand-dot {
    width: 34px;
    height: 34px;
    border-radius: 50%;
    background: var(--ink);
  }
  .brand-name {
    font-family: "Montserrat", sans-serif;
    font-weight: 400;
    font-size: 70px;
    letter-spacing: 7px;
    line-height: 80px;
    color: var(--ink);
  }
  .tagline {
    position: absolute;
    top: 292px;
    left: 0;
    width: 686px;
    margin: 0;
    line-height: 38px;
    text-align: center;
    font-family: "Encode Sans Condensed", sans-serif;
    font-weight: 500;
    font-size: 31px;
    letter-spacing: -0.4px;
    color: var(--ink-soft);
  }
  .person {
    position: absolute;
    top: 466px;
    left: 0;
    width: 686px;
    text-align: center;
    font-family: "Montserrat", sans-serif;
  }
  .person-name {
    font-weight: 700;
    font-size: 50px;
    line-height: 60px;
  }
  .person-name .surname { color: var(--accent); }
  .person-role {
    font-weight: 400;
    font-size: 39px;
    line-height: 42px;
  }
  .rule {
    position: absolute;
    left: 74px;
    width: 540px;
    height: 2px;
    background: var(--rule);
  }
  .rule.upper { top: 678px; }
  .rule.lower { top: 1097px; }
  .contact-list {
    position: absolute;
    top: 700px;
    left: 108px;
    margin: 0;
    padding: 0;
    list-style: none;
    font-family: "Cabin", sans-serif;
    font-size: 30px;
    color: var(--ink);
  }
  .contact-item {
    position: absolute;
    left: 0;
    display: flex;
    align-items: center;
    white-space: nowrap;
  }
  .contact-item svg {
    width: 48px;
    height: 48px;
    flex: none;
    margin-right: 12px;
    fill: #333333;
  }
  .contact-item.address { top: 0; align-items: flex-start; line-height: 42px; }
  .contact-item.address svg { height: 60px; margin-top: 4px; }
  .contact-item.phone { top: 120px; }
  .contact-item.fax { top: 171px; }
  .contact-item.mobile { top: 223px; }
  .contact-item.email { top: 279px; }
  .contact-item.web { top: 330px; }
</style>
</head>
<body>
<main class="card">
  <div class="accent-tab top"></div>

  <header class="brand">
    <span class="brand-dot"></span>
    <span class="brand-name">TALLIVO</span>
  </header>
  <p class="tagline">ALLOCATION &amp; SCHEDULING FOR FIELD CREWS</p>

  <section class="person">
    <div class="person-name">Jack <span class="surname">Dane</span></div>
    <div class="person-role">Job title here</div>
  </section>

  <div class="rule upper"></div>

  <ul class="contact-list">
    <li class="contact-item address">
      <svg viewBox="0 0 24 30" aria-hidden="true"><path d="M12 0C5.4 0 1 4.8 1 10.6 1 18 12 30 12 30s11-12 11-19.4C23 4.8 18.6 0 12 0zm0 15a4.5 4.5 0 1 1 0-9 4.5 4.5 0 0 1 0 9z"/></svg>
      <span>PO Box 512<br>Elm Vale NSW 1620</span>
    </li>
    <li class="contact-item phone">
      <svg viewBox="0 0 48 48" aria-hidden="true"><path d="M4 16c0-5 9-8 20-8s20 3 20 8v3h-9v-4c-3-1-7-1.5-11-1.5S16 14 13 15v4H4z"/><path d="M10 22h28l4 16H6z"/><circle cx="24" cy="30" r="5" fill="#f0f0f0"/></svg>
      <span>502 481 7306</span>
    </li>
    <li class="contact-item fax">
      <svg viewBox="0 0 48 48" aria-hidden="true"><rect x="16" y="4" width="22" height="16"/><rect x="6" y="16" width="8" height="28" rx="2"/><rect x="16" y="22" width="28" height="22" rx="2"/><rect x="20" y="27" width="20" height="3" fill="#f0f0f0"/><rect x="20" y="33" width="4" height="3" fill="#f0f0f0"/><rect x="28" y="33" width="4" height="3" fill="#f0f0f0"/><rect x="36" y="33" width="4" height="3" fill="#f0f0f0"/></svg>
      <span>502 481 7319</span>
    </li>
    <li class="contact-item mobile">
      <svg viewBox="0 0 48 48" aria-hidden="true"><rect x="13" y="2" width="22" height="44" rx="3"/><rect x="16" y="8" width="16" height="28" fill="#f0f0f0"/><circle cx="24" cy="41" r="2" fill="#f0f0f0"/></svg>
      <span>502 5538 4162</span>
    </li>
    <li class="contact-item email">
      <svg viewBox="0 0 48 48" aria-hidden="true"><path d="M4 10h40v28H4zm3 3v22h34V13zm0 0l17 14 17-14v3L24 30 7 16zm0 22l12-11 2 1.6L9 35zm34 0L29 24l-2 1.6L39 35z" fill-rule="evenodd"/></svg>
      <span>contact@tallivo.com.au</span>
    </li>
    <li class="contact-item web">
      <svg viewBox="0 0 48 48" aria-hidden="true"><path d="M8 10h32v22H8zm3 3v16h26V13z" fill-rule="evenodd"/><path d="M2 34h44l-3 4H5z"/></svg>
      <span>www.tallivo.com.au</span>
    </li>
  </ul>

  <div class="rule lower"></div>

  <div class="accent-tab bottom"></div>
</main>
</body>
</html>
```